Venture Capital Investment Firm

We are looking to overhaul our existing website (substantially), with only using the same logos (which we can provide).
We are an investment firm that focuses on making loans to late stage technology companies. Our site should ultimately look like other venture capital firms, and look modern and fresh. We have an existing website www.norvellhub.com which this will be replacing, although we will be using a lot of the existing written content, and potentially the numbers of pages we will need, we are not wed to anything else. Please feel free to shoot any questions at any time and thank you in advance for your help!
Websites we like as examples:
https://www.tesmarkfund.com/
https://www.brindlewoodpartners.com/
Target Market(s)
Potential investors who will invest in our firm, as well as potentially companies that are looking to borrow money from us.
Coding
Coded - Design and coding required
Number of Pages Required
5+ page
Colors
Designer to choose colors to be used in the design.
Look and feel

```html
<!DOCTYPE html>
<html lang="en">
<head>
<meta charset="utf-8">
<title>Halvorsen Crest Investment Partners</title>
<link rel="stylesheet" href="https://fonts.googleapis.com/css2?family=Cinzel:wght@600;700&family=Montserrat:wght@400;500&family=Oswald:wght@400;600&display=swap">
<style>
:root{
  --navy:#08086e;
  --navy-deep:#05055a;
  --ink:#0a0a4a;
  --band:#2b2b90;
  --panel:#f3f3f5;
  --soft:#f4f4f4;
  --text:#6a6a78;
  --white:#ffffff;
  --accent:#9ab8f0;
}
*{margin:0;padding:0;box-sizing:border-box}
html,body{width:1200px;height:3563px;overflow:hidden}
body{position:relative;background:var(--white);font-family:"Montserrat",sans-serif;color:var(--text)}
.abs{position:absolute}
.serif{font-family:"Cinzel",serif;font-weight:700;letter-spacing:.5px;text-transform:uppercase}

/* hero */
.hero{left:0;top:0;width:1200px;height:676px;background:linear-gradient(135deg,#0a0a70 0%,#17178a 40%,#2436a6 65%,#10107a 100%)}
.hero-art{left:620px;top:140px;width:520px;height:536px;border-radius:50%;background:radial-gradient(ellipse at 50% 50%,rgba(140,176,240,.85) 0%,rgba(70,105,210,.6) 40%,rgba(20,20,130,0) 72%)}
.brand{display:flex;align-items:center;gap:12px;color:var(--white);font-family:"Cinzel",serif;font-weight:700;font-size:24px;letter-spacing:1px;white-space:nowrap}
.brand .dot{width:34px;height:34px;border-radius:50%;background:var(--white)}
.brand-top{left:77px;top:22px}
.nav{left:480px;top:31px;width:640px;display:flex;justify-content:flex-end;gap:26px;align-items:center;white-space:nowrap}
.nav a{color:#d8dcf5;text-decoration:none;font-size:14.5px;letter-spacing:.5px;white-space:nowrap;display:flex;align-items:center}
.nav .mark{display:inline-block;width:8px;height:8px;border-radius:50%;background:#d8dcf5;margin-right:6px}
.hero-title{left:79px;top:236px;color:var(--white);font-family:"Oswald",sans-serif;font-weight:600;font-size:40px;line-height:47px;text-transform:uppercase}
.hero-sub{left:79px;top:386px;color:#e6e8ff;font-family:"Oswald",sans-serif;font-size:18px;text-transform:uppercase}
.btn{display:flex;align-items:center;justify-content:center;border-radius:26px;font-family:"Cinzel",serif;font-weight:700;font-size:18px;letter-spacing:.5px;text-decoration:none;white-space:nowrap}
.btn-light{background:var(--white);color:var(--ink)}
.btn-dark{background:var(--navy-deep);color:var(--white)}
.hero-btn{left:77px;top:441px;width:187px;height:51px}

/* about */
.about-photo{left:76px;top:755px;width:396px;height:396px;border-radius:50%;background:radial-gradient(circle at 50% 40%,#3b5fff 0%,#1414b8 50%,#070760 100%)}
.about-panel{left:413px;top:814px;width:711px;height:588px;background:var(--panel)}
.about-title{left:499px;top:868px;color:var(--ink);font-size:37px;line-height:47px;white-space:nowrap}
.about-kicker{left:507px;top:977px;color:#222;font-size:15px;font-weight:500}
.about-copy{left:508px;top:1011px;width:530px;font-size:14px;line-height:27px}
.exp-label{left:510px;top:1114px;color:#222;font-size:15px;font-weight:500}
.stat{top:1148px;width:200px;text-align:center}
.stat b{display:block;color:var(--ink);font-family:"Cinzel",serif;font-weight:700;font-size:38px;line-height:44px}
.stat span{display:block;font-size:13.5px;line-height:27px;margin-top:4px}
.about-btn{left:509px;top:1284px;width:182px;height:51px}

/* testimonials */
.voices{left:0;top:1496px;width:1200px;height:474px;background:var(--soft)}
.section-title{width:1200px;left:0;text-align:center;font-size:40px}
.voices-title{top:1565px;color:var(--ink)}
.avatar{left:76px;top:1668px;width:158px;height:158px;border-radius:50%;border:3px solid var(--ink);background:radial-gradient(circle,#caa48a 0%,#a07e6a 60%,#6b5148 100%)}
.quote{left:281px;top:1675px;width:830px;font-size:14px;line-height:27px}
.quote-by{left:281px;top:1772px;color:var(--ink);font-size:20px}
.dots{left:530px;top:1875px;display:flex;gap:16px}
.dots i{width:15px;height:15px;border-radius:50%;border:2px solid var(--navy)}
.dots i.on{background:var(--navy)}

/* team */
.team{left:0;top:1970px;width:1200px;height:610px;background:var(--navy)}
.team-title{top:2024px;color:var(--white)}
.member{top:2096px;width:323px;height:312px;background:radial-gradient(ellipse at 50% 40%,#9a9a9a 0%,#6e6e6e 30%,#e8e8e8 60%,#f2f2f2 100%)}
.member .band{position:absolute;left:0;bottom:0;width:100%;height:83px;background:rgba(43,43,144,.92);text-align:center;color:var(--white);padding-top:16px}
.member h3{font-family:"Cinzel",serif;font-weight:700;font-size:21px}
.member p{font-size:14px;margin-top:3px}
.team-btn{left:437px;top:2440px;width:326px;height:51px}

/* news */
.news-title{top:2662px;color:var(--ink)}
.card{top:2759px;width:323px;background:var(--soft);padding:26px 20px 30px 20px}
.card h4{color:var(--ink);font-size:15.5px;font-weight:500;line-height:22px}
.card time{display:block;font-family:"Cinzel",serif;font-size:15px;color:#8a8a96;margin-top:10px}
.card p{font-size:14px;line-height:27px;margin-top:18px}
.card a{display:inline-block;font-family:"Cinzel",serif;font-weight:700;font-size:17px;color:var(--ink);margin-top:14px}

/* footer */
.footer{left:0;top:3153px;width:1200px;height:345px;background:var(--navy)}
.brand-foot{left:97px;top:3278px;font-size:26px}
.legal{left:174px;top:3342px;color:#b9c0f0;font-size:14.5px}
.foot-h{top:3184px;color:var(--white);font-size:18px}
.foot-row{left:435px;display:flex;gap:20px;color:#c7cdf5;font-size:14px;line-height:27px}
.foot-row svg{flex:none;width:26px;margin-top:4px}
.news-text{left:792px;top:3227px;width:330px;color:#c7cdf5;font-size:14px;line-height:27px}
.field{left:791px;width:322px;height:46px;background:#17178a;color:#c7cdf5;font-size:14px;padding:15px 16px}
.sub-btn{left:791px;top:3404px;width:160px;height:50px}
.copyright{left:0;top:3498px;width:1200px;height:65px;background:#f0f0f2;color:#333;font-size:14px;text-align:center;line-height:65px}
</style>
</head>
<body>

<section class="abs hero" role="img" aria-label="Blue-tinted photo of glass office towers seen from below"></section>
<div class="abs hero-art" role="img" aria-label="Close-up of a glass skyscraper facade in light blue"></div>

<div class="abs brand brand-top"><span class="dot"></span>HALVORSEN CREST</div>
<nav class="abs nav">
  <a href="#"><span class="mark"></span>HOME</a>
  <a href="#">STRATEGY</a>
  <a href="#">ABOUT US</a>
  <a href="#">TEAM</a>
  <a href="#">NEWS</a>
  <a href="#">CONTACT</a>
  <a href="#">INVESTORS</a>
</nav>

<h1 class="abs hero-title">We are a global structured<br>credit investment firm<br>focused on the</h1>
<p class="abs hero-sub">Healthcare and technology industries</p>
<a class="abs btn btn-light hero-btn" href="#">LEARN MORE</a>

<div class="abs about-panel"></div>
<div class="abs about-photo" role="img" aria-label="Glowing blue brain inside a light bulb"></div>
<h2 class="abs serif about-title">Halvorsen Crest Started<br>With A Big Idea</h2>
<p class="abs about-kicker">FINANCE PROVEN INNOVATION WITH A DIFFERENT APPROACH</p>
<p class="abs about-copy">Halvorsen Crest is a private investment firm unique in its dual focus on life science and technology credit opportunit- ies.&nbsp; Our ambidextrous approach to investing reflects a broad recognition and appreciation for.</p>
<p class="abs exp-label">OUR EXPERIENCE</p>
<div class="abs stat" style="left:494px"><b>$1.2B</b><span>Over $1.2B invested<br>by our partners</span></div>
<div class="abs stat" style="left:682px"><b>40+</b><span>40 Life science and<br>technology investments</span></div>
<div class="abs stat" style="left:901px"><b>12+</b><span>Over a decade innovating<br>financing structures</span></div>
<a class="abs btn btn-dark about-btn" href="#">LEARN MORE</a>

<section class="abs voices"></section>
<h2 class="abs serif section-title voices-title">What Our Partners Say</h2>
<div class="abs avatar" role="img" aria-label="Portrait of a partner"></div>
<p class="abs quote">Lorem Ipsum is simply dummy text of the printing and typesetting industry. Lorem Ipsum has been the industry's standard dummy text ever since the 1500s, when an unknown printer took a galley of type and scrambled it to make a type specimen book.</p>
<p class="abs serif quote-by">CEO - Partner Name</p>
<div class="abs dots"><i class="on"></i><i></i><i></i><i></i><i></i></div>

<section class="abs team"></section>
<h2 class="abs serif section-title team-title">Meet Our Team</h2>
<div class="abs member" style="left:77px" role="img" aria-label="Black and white portrait of a managing partner">
  <div class="band"><h3>ELLIOT MARROW</h3><p>Managing Partner</p></div>
</div>
<div class="abs member" style="left:438px" role="img" aria-label="Black and white portrait of a managing partner">
  <div class="band"><h3>DEVAN OKAFOR</h3><p>Managing Partner</p></div>
</div>
<div class="abs member" style="left:799px" role="img" aria-label="Black and white portrait of a partner">
  <div class="band"><h3>GRANT PELLOW</h3><p>Partner</p></div>
</div>
<a class="abs btn btn-light team-btn" href="#">KNOW MORE ABOUT TEAM</a>

<h2 class="abs serif section-title news-title">Halcrest News</h2>
<article class="abs card" style="left:77px">
  <h4>Halvorsen Crest completes structured debt investment in LumaPath</h4>
  <time>April 30, 2018</time>
  <p>Halvorsen Crest Investment Partners ("Halvorsen Crest") announced today that it has completed a structured...</p>
  <a href="#">READ MORE</a>
</article>
<article class="abs card" style="left:438px">
  <h4>Halvorsen Crest completes $22,000,000 structured debt investment in Surveyline</h4>
  <time>October 19, 2016</time>
  <p>Halvorsen Crest Investment Partners ("Halvorsen Crest") announced today that it has completed a $22,000,000...</p>
  <a href="#">READ MORE</a>
</article>
<article class="abs card" style="left:799px">
  <h4>Korvant Semiconductor acquired by Brightridge for $55,000,000</h4>
  <time>April 4, 2016</time>
  <p>Brightridge Optics, Inc., a leading supplier of advanced semiconductor communications components for...</p>
  <a href="#">READ MORE</a>
</article>

<footer class="abs footer"></footer>
<div class="abs brand brand-foot"><span class="dot"></span>HALVORSEN CREST</div>
<a class="abs legal" href="#">Legal Disclaimer</a>

<h3 class="abs serif foot-h" style="left:435px">Contact Us</h3>
<div class="abs foot-row" style="top:3226px">
  <svg viewBox="0 0 20 28" height="28"><path d="M10 0a10 10 0 0 0-10 10c0 7 10 18 10 18s10-11 10-18A10 10 0 0 0 10 0zm0 14a4 4 0 1 1 0-8 4 4 0 0 1 0 8z" fill="#fff"/></svg>
  <div>SAN FRANCISCO<br>2200 Harlow Street #310<br>San Francisco, CA&nbsp; 94107</div>
</div>
<div class="abs foot-row" style="top:3327px">
  <svg viewBox="0 0 24 18" height="18"><rect width="24" height="18" rx="2" fill="#fff"/><path d="M1 2l11 8 11-8" stroke="#08086e" stroke-width="2" fill="none"/></svg>
  <div>GENERAL INQUIRIES : :<br>inquiries@halvorsencrest.com</div>
</div>
<div class="abs foot-row" style="top:3398px">
  <svg viewBox="0 0 24 18" height="18"><rect width="24" height="18" rx="2" fill="#fff"/><path d="M1 2l11 8 11-8" stroke="#08086e" stroke-width="2" fill="none"/></svg>
  <div>MEDIA INQUIRIES :<br>media@halvorsencrest.com</div>
</div>

<h3 class="abs serif foot-h" style="left:792px">Newsletter</h3>
<p class="abs news-text">Would you like to receive our exclusive news and update for signup our newsletter !</p>
<div class="abs field" style="top:3293px">Enter Name *</div>
<div class="abs field" style="top:3348px">Enter Email *</div>
<a class="abs btn btn-light sub-btn" href="#">SUBSCRIBE</a>

<div class="abs copyright">©2019 Halvorsen Crest Investment Partners LLC.&nbsp; All Rights Reserved.</div>

</body>
</html>
```